Wordpress Design Project

Hi,

I would like a more modern colourful design doing for my website ZAP Lnx (www.za%plnx.com - remove percentage). But I do still want to keep the same sort of colors, just maybe lighter. More interesting.

I want the inside pages to NOT all look the same with just boring text.

I want the site to look more appealing and maybe a new logo.
Updates

I would like to mention I would prefer to keep the same logo after rethinking it (possibly a slight refresh of the logo if you feel its a good idea) and the same color scheme as at present.

Saves us rebranding a lot of our apps, tools online ads etc.

Also I thought it is worth mentioning we have 2 parts to the site. The front end and the logged in area. It would be good if when making the front end you keep in mind the back end at http://p.za%plnx.com (remove percentage). We can only edit this limitedly (can edit the entire footer, the logo and full CSS of it). Would be good if we could make sure the header and footer can be used on the back end as well maybe to make it match.

I also want layouts making not just for the homepage. Obviously every page will basically be the same but I don't want all the other pages to just be 'text' and no real layout.

You can see out main pages on the website at the moment, I want those other pages to be laid out nice and differently as well. For example the testimonials page could be more interesting with speech bubbles and pictures of each person (just use placeholders). The affiliates page could be a description and then a nice fancy list of features why to join etc. 

Nothing overly complicated but I think it makes the whole site seem a lot better.

Target Market(s)

Affiliate Marketing. International.

Requirements
Must have
• Needs to be more room for links across the navigation at the top, also sub menus (at present we have a lot of pages which are hidden deep within other pages).
Nice to have
• Lists of features for advertisers and affiliates on the homepage part.

Menu items and buttons have nice hover over effects.

I want to get across on our pages all the different unique features we have.

Maybe some kind of slider which has past offer logos in, just use example logos.

```html
<!DOCTYPE html>
<html lang="en">
<head>
<meta charset="utf-8">
<title>ZAP Lnx – International Affiliate Network</title>
<link rel="stylesheet" href="https://fonts.googleapis.com/css2?family=Roboto+Condensed:wght@400;700&family=Open+Sans:wght@400;600;700&display=swap">
<style>
:root{
  --orange:#f7941d;
  --blue-nav:#1468a8;
  --teal:#1ba6c9;
  --navy:#1d4f86;
  --ink:#222222;
  --text:#7a7a7a;
  --band:#e9f2f3;
  --panel:#f0f0f0;
  --line:#dcdcdc;
  --white:#ffffff;
}
*{box-sizing:border-box;margin:0;padding:0}
html,body{width:796px;height:1200px;overflow:hidden}
body{position:relative;background:var(--white);font-family:"Open Sans",sans-serif;color:var(--text)}
.abs{position:absolute}

/* header */
.brand{left:113px;top:20px;font:700 30px/1 "Roboto Condensed",sans-serif;color:var(--ink);display:flex;align-items:center;gap:9px}
.brand .mark{width:14px;height:14px;background:var(--ink)}
.tab{top:0;height:25px;width:82px;border-radius:0 0 14px 14px;font:400 11px/25px "Roboto Condensed",sans-serif;color:#fff;text-align:center}
.tab.login{left:539px;background:linear-gradient(#2aa6e6,#137cc4)}
.tab.signup{left:621px;background:linear-gradient(#fdb24a,#f48a12)}
.phone{left:553px;top:37px;font:700 16px "Roboto Condensed",sans-serif;color:#111}

/* nav */
.nav{left:0;top:68px;width:796px;height:25px;background:linear-gradient(#f9a231,#ef860f)}
.nav ul{list-style:none;display:flex;position:absolute;left:117px;top:0}
.nav li{font:400 13px/25px "Roboto Condensed",sans-serif;color:#fff;padding:0 9px;margin-right:2px}
.nav li.current{background:var(--blue-nav)}

/* hero */
.hero{left:0;top:93px;width:796px;height:349px;background:radial-gradient(ellipse at 45% 40%,#43b3ec,#1585cf 60%,#0f6fb7)}
.hero-title{left:0;width:796px;text-align:center;font-family:"Roboto Condensed",sans-serif;color:#fff6dc;font-weight:700}
.hero-title.small{top:101px;font-size:21px}
.hero-title.big{top:120px;font-size:31px}
.world-map{left:130px;top:170px;width:490px;height:210px;border-radius:40px;background:linear-gradient(160deg,#8fd3f7,#5db9ec);opacity:.85}
.join{left:334px;top:392px;width:130px;height:28px;border-radius:14px;background:linear-gradient(#fba73a,#e9750c);border:2px solid #fff;font:700 14px/24px "Roboto Condensed",sans-serif;color:#fff;text-align:center}
.dots{left:382px;top:430px;display:flex;gap:4px}
.dots span{width:7px;height:7px;border-radius:50%;background:#fff}
.dots span.on{background:var(--orange)}
.ad-types{left:624px;top:106px;width:76px;height:328px;border-radius:38px;background:#0c5f9c;border:3px solid #5fb6ea;overflow:hidden}
.ad-type{height:64px;border-bottom:1px solid #3f8ec7;display:flex;flex-direction:column;align-items:center;justify-content:flex-end;padding-bottom:4px;color:#fff;font:700 9px/1.05 "Roboto Condensed",sans-serif;text-align:center}
.ad-type:last-child{border-bottom:0}
.ad-type small{font-size:6px;font-weight:400}
.ad-type svg{margin-bottom:4px}

/* intro band */
.band{left:0;top:442px;width:796px;height:143px;background:linear-gradient(#f3f8f8,var(--band))}
.intro{top:451px;width:292px}
.intro h2{font:700 20px/1.2 "Roboto Condensed",sans-serif;color:var(--orange)}
.intro p{font-size:9.3px;line-height:15px;color:#555;margin-top:5px}
.btn-signup{width:114px;height:29px;border-radius:4px;background:linear-gradient(#ffd75a,#f5b417);font:700 14px/29px "Roboto Condensed",sans-serif;color:#333;text-align:center;top:534px}
.rule{left:0;top:579px;width:796px;height:6px;background:repeating-linear-gradient(45deg,#dfe7e8 0 2px,#eef4f4 2px 4px)}

/* sidebar */
.login-box{left:100px;top:600px;width:141px;height:164px;background:var(--panel);border-radius:4px;padding:10px 13px}
.login-box h3,.side h3{font:400 14px "Roboto Condensed",sans-serif;color:#111}
.field{margin-top:8px;height:26px;background:#fff;border-radius:4px;font-size:9.5px;color:#222;padding:7px 7px}
.forgot{font-size:8px;color:#222;margin-top:9px}
.login-row{display:flex;align-items:center;gap:6px;margin-top:9px;font-size:8.5px;color:#222}
.login-btn{padding:4px 6px;border:1px solid #999;border-radius:4px;background:linear-gradient(#fff,#ddd);font-weight:600}
.side{left:100px;width:141px}
.side ul{list-style:none;margin-top:7px}
.side li{font-size:8.5px;color:#777;padding:3px 0 3px 8px;border-bottom:1px solid #e4e4e4;position:relative}
.side li:last-child{border-bottom:0}
.side li::before{content:"›";position:absolute;left:0}
.social{display:flex;gap:11px;margin-top:8px}
.social span{width:26px;height:26px;border-radius:3px}

/* main */
.welcome{left:266px;top:598px;width:432px}
.welcome h1{font:400 20px "Roboto Condensed",sans-serif;color:var(--teal)}
.welcome p{font-size:8.6px;line-height:13px;color:var(--text);margin-top:7px;letter-spacing:-.1px}
.why{left:267px;top:788px;width:202px;height:149px;background:var(--orange);border-radius:4px;padding:10px 12px;color:#fff}
.why h3{font:400 15px "Roboto Condensed",sans-serif}
.why ul{list-style:none;margin-top:8px}
.why li{font-size:8.5px;line-height:15.5px}
.why li.two{line-height:12px;padding:2px 0}
.why li::before{content:"› "}
.testimonial{left:496px;top:794px;width:200px}
.testimonial h3{font:400 14px "Roboto Condensed",sans-serif;color:var(--teal)}
.testimonial blockquote{font-size:8.4px;line-height:14.6px;color:#555;margin-top:7px;padding-bottom:8px;border-bottom:1px solid var(--line)}
.testimonial cite{display:block;text-align:right;font-style:normal;font-size:9px;color:#222;margin-top:9px;padding-right:18px}

/* advertisers */
.adv-head{left:100px;top:974px;width:596px;height:18px}
.adv-head::before{content:"";position:absolute;left:0;right:0;top:9px;border-top:1px solid var(--line)}
.adv-head h2{position:relative;margin:0 auto;width:100px;background:#fff;text-align:center;font:400 14px "Roboto Condensed",sans-serif;color:var(--navy)}
.partners{left:100px;top:1005px;width:596px;display:flex;justify-content:space-between}
.partner{width:80px;height:58px;display:flex;flex-direction:column;align-items:center;justify-content:center;gap:5px;font:600 9px "Open Sans",sans-serif}
.partner .mark{width:30px;height:30px}
.partner.a{color:#7a1416}.partner.a .mark{background:#7a1416}
.partner.b{color:#b0141c}.partner.b .mark{background:#f3c12c;border-radius:50%}
.divider{left:100px;top:1082px;width:596px;border-top:1px solid var(--line)}
.badges{left:198px;top:1105px;display:flex;gap:18px}
.badge{width:88px;height:26px;border:1px solid #c9dde6;border-radius:2px;background:#f7fbfc;display:flex;align-items:center;padding:0 5px}
.badge span{width:16px;height:16px;border-radius:3px;background:#9fbfd0}

/* footer */
.footer{left:0;top:1143px;width:796px;height:57px;background:linear-gradient(#eef3f3,#e6eded);border-top:5px solid #dfe7e8}
.footer nav{position:absolute;top:12px;left:0;width:796px;text-align:center;font-size:8.5px;color:#222}
.footer nav span{margin:0 14px}
.footer p{position:absolute;top:33px;width:796px;text-align:center;font-size:8px;color:#777}
</style>
</head>
<body>

<header>
  <div class="abs brand"><span class="mark"></span>ZAP Lnx</div>
  <a class="abs tab login">LOGIN</a>
  <a class="abs tab signup">SIGN UP</a>
  <div class="abs phone">+44 (0)1500 400219</div>
</header>

<nav class="abs nav">
  <ul>
    <li class="current">HOME</li><li>ABOUT US</li><li>OUR BLOG</li><li>TESTIMONIALS</li><li>AFFILIATES</li><li>ADVERTISERS</li><li>CONTACT US</li>
  </ul>
</nav>

<section class="abs hero"></section>
<div class="abs hero-title small">INTERNATIONAL</div>
<div class="abs hero-title big">AFFILIATE NETWORK</div>
<div class="abs world-map" role="img" aria-label="World map with orange location pins marking network partners"></div>
<div class="abs join">JOIN US TODAY!</div>
<div class="abs dots"><span class="on"></span><span></span><span></span></div>

<aside class="abs ad-types">
  <div class="ad-type">
    <svg width="28" height="22" viewBox="0 0 28 22"><rect x="1" y="1" width="26" height="20" fill="none" stroke="#fff" stroke-width="2"/><rect x="9" y="6" width="10" height="10" fill="#fff"/></svg>
    BANNER<small>FLASH · JPG · GIF</small></div>
  <div class="ad-type">
    <svg width="18" height="28" viewBox="0 0 18 28"><rect x="1" y="1" width="16" height="26" rx="3" fill="none" stroke="#fff" stroke-width="2"/><rect x="4" y="5" width="10" height="15" fill="#fff"/></svg>
    MOBILE ADS</div>
  <div class="ad-type">
    <svg width="30" height="20" viewBox="0 0 30 20"><rect x="1" y="1" width="28" height="18" fill="#fff"/><path d="M1 1l14 10L29 1" fill="none" stroke="#0c5f9c" stroke-width="2"/></svg>
    EMAIL<br>MARKETING</div>
  <div class="ad-type">
    <svg width="30" height="22" viewBox="0 0 30 22"><rect x="1" y="1" width="28" height="20" fill="none" stroke="#fff" stroke-width="2"/><rect x="5" y="5" width="9" height="7" fill="#fff"/><path d="M17 6h8M17 10h8M5 15h20" stroke="#fff" stroke-width="2"/></svg>
    TEXT ADS</div>
  <div class="ad-type">
    <svg width="26" height="26" viewBox="0 0 26 26"><g fill="none" stroke="#fff" stroke-width="3"><rect x="2" y="9" width="12" height="7" rx="3.5" transform="rotate(45 8 12.5)"/><rect x="12" y="10" width="12" height="7" rx="3.5" transform="rotate(45 18 13.5)"/></g></svg>
    LINKS</div>
</aside>

<section class="abs band"></section>
<div class="abs intro" style="left:100px">
  <h2>AFFILIATES</h2>
  <p>Get access to a wide range of top performing offers for your websites and email marketing lists. Fresh and exclusive offers to promote. Join over 2,000 affiliates already signed up to ZAP Lnx.</p>
</div>
<div class="abs intro" style="left:410px">
  <h2>ADVERTISERS</h2>
  <p>Generate sales/leads to your website instantly with the ZAP Lnx Affiliate Network. Only pay on performance, no monthly or setup fees. ZAP Lnx takes the risk out of advertising.</p>
</div>
<div class="abs btn-signup" style="left:100px">SIGN UP NOW</div>
<div class="abs btn-signup" style="left:410px">SIGN UP NOW</div>
<div class="abs rule"></div>

<aside class="abs login-box">
  <h3>ACCOUNT LOGIN</h3>
  <div class="field">Email</div>
  <div class="field" style="margin-top:12px">Password</div>
  <div class="forgot">Forgot Password</div>
  <div class="login-row"><span class="login-btn">LOGIN</span>or Sign Up</div>
</aside>

<aside class="abs side" style="top:784px">
  <h3>RECENT BLOG POSTS</h3>
  <ul><li>New Offers For China</li><li>NEW: Banner Rotators</li><li>New Offers</li></ul>
</aside>
<aside class="abs side" style="top:883px">
  <h3>SOCIAL NETWORKING</h3>
  <div class="social"><span style="background:#3b5a98"></span><span style="background:#5dbbe8"></span><span style="background:#c4221c"></span><span style="background:#1d7cb3"></span></div>
</aside>

<main>
  <article class="abs welcome">
    <h1>WELCOME TO ZAP LNX</h1>
    <p>Welcome to the ZAP Lnx affiliate network. On time payments, hot &amp; exclusive CPL/CPA offers, fast support and low fees for advertisers, is the making of a leading affiliate network!</p>
    <p>ZAP Lnx offer a wide range of advertisers for your websites. So you can start monetizing your traffic or get an additional revenue stream, today.</p>
    <p>With the ZAP Lnx Affiliate Network we focus on lead generation offers. We have a range of competitions, surveys, incentives and gambling offers. Whatever the industry, you will be able to find offers to suit your traffic.</p>
    <p>ZAP Lnx is a powerful performance-based internet marketing network dedicated to advertisers to affiliates through its powerful affiliate network.</p>
  </article>

  <section class="abs why">
    <h3>WHY JOIN ZAP LNX?</h3>
    <ul>
      <li>High Payouts</li><li>Reliable Tracking</li><li>Great Affiliate Support</li><li>Exclusive Offers</li>
      <li class="two">Monthly/Bi-monthly/Weekly Payments<br>&nbsp;&nbsp;(more info)</li>
      <li>View Stats on Your Mobile</li>
    </ul>
  </section>

  <section class="abs testimonial">
    <h3>TESTIMONIALS</h3>
    <blockquote>"I decided to start using ZAP Lnx after using several other ZAP sites. I was impressed with the customer service and support provided in comparison to some other networks I have used. ZAP Lnx also has a large range of offers, retailers so is the perfect solution to earning commission. Payments are always on-time too."</blockquote>
    <cite>Mara Quell – Sitebloom</cite>
  </section>
</main>

<div class="abs adv-head"><h2>ADVERTISERS</h2></div>
<div class="abs partners">
  <div class="partner a"><span class="mark"></span>Northwind Co</div>
  <div class="partner b"><span class="mark"></span>Brightpost</div>
  <div class="partner a"><span class="mark"></span>Northwind Co</div>
  <div class="partner b"><span class="mark"></span>Brightpost</div>
  <div class="partner a"><span class="mark"></span>Northwind Co</div>
  <div class="partner b"><span class="mark"></span>Brightpost</div>
  <div class="partner a"><span class="mark"></span>Northwind Co</div>
</div>
<div class="abs divider"></div>
<div class="abs badges">
  <div class="badge"><span></span></div>
  <div class="badge"><span></span></div>
  <div class="badge"><span></span></div>
  <div class="badge"><span></span></div>
</div>

<footer class="abs footer">
  <nav><span>Affiliate Terms &amp; Conditions</span>|<span>Advertiser Terms &amp; Conditions</span>|<span>Privacy Policy &amp; Cookies</span>|<span>FAQ</span>|<span>Contact Us</span></nav>
  <p>© 2013 ZAP Media UK Ltd - All Rights Reserved.</p>
</footer>

</body>
</html>
```